Business Card Design Project

Doctor, Pain Management. Need a new business card design with appointment info on the back. New address is 18 Corvell Road, Suite 304, Brisdale, NJ 07391. Right now I believe the rest of the information is staying the same.

```html
<!DOCTYPE html>
<html lang="en">
<head>
<meta charset="utf-8">
<title>Harbor Pain Management – Business Card</title>
<link rel="stylesheet" href="https://fonts.googleapis.com/css2?family=Lato:wght@400;700&display=swap">
<style>
  :root {
    --backdrop: #2a2a2a;
    --card-front: #f3f3f3;
    --card-back: #ffffff;
    --ink: #1f1f1f;
    --ink-soft: #2e2e2e;
    --muted: #8a8a8a;
    --rule: #9a9a9a;
    --accent: #e8590c;
  }
  * { margin: 0; padding: 0; box-sizing: border-box; }
  html, body { width: 1200px; height: 1200px; overflow: hidden; }
  body {
    background: var(--backdrop);
    font-family: "Lato", Arial, sans-serif;
    color: var(--ink);
    position: relative;
  }
  .card {
    position: absolute;
    top: 310px;
    width: 364px;
    height: 594px;
    box-shadow: 2px 3px 6px rgba(0,0,0,.45);
    text-align: center;
  }
  .card--front { left: 234px; background: var(--card-front); }
  .card--back  { left: 627px; width: 369px; background: var(--card-back); }
  .card > * { position: absolute; left: 0; right: 0; }

  .brand-mark {
    display: flex; align-items: center; justify-content: center; gap: 10px;
    font-weight: 700; color: var(--ink);
    letter-spacing: 1px;
  }
  .brand-mark__dot { border-radius: 50%; background: var(--accent); }
  .card--front .brand-mark { top: 415px; top: 105px; font-size: 50px; line-height: 60px; }
  .card--front .brand-mark__dot { width: 16px; height: 16px; }
  .brand-name { top: 180px; font-size: 25px; line-height: 34px; color: var(--ink); }

  .doctor-name { top: 295px; font-size: 21px; font-weight: 700; color: var(--accent); letter-spacing: .3px; }
  .doctor-title { top: 321px; font-size: 16px; color: var(--ink-soft); }

  .icon-row {
    top: 364px; left: 59px; right: 52px;
    display: flex; align-items: center; gap: 6px;
  }
  .icon-row__rule { flex: 1; height: 1px; background: var(--ink-soft); }
  .icon-row__icon { width: 22px; height: 22px; background: var(--accent); display: flex; align-items: center; justify-content: center; }
  .icon-row__icon svg { width: 15px; height: 15px; }

  .contact-list { top: 396px; list-style: none; font-size: 16px; line-height: 21.5px; color: var(--ink-soft); }
  .divider { top: 493px; left: 115px; right: 53px; height: 1px; background: var(--ink-soft); width: 196px; margin: 0 auto; left: 0; right: 0; }
  .address { top: 505px; font-size: 16px; line-height: 21.5px; color: var(--ink-soft); font-style: normal; }

  .card--back .brand-mark { top: 90px; font-size: 92px; line-height: 110px; }
  .card--back .brand-mark__dot { width: 26px; height: 26px; }
  .appointment-title { top: 267px; font-size: 25px; letter-spacing: .5px; color: var(--ink); }

  .appt-field {
    left: 28px; right: 27px;
    text-align: left; font-size: 22px; color: var(--muted);
    border-bottom: 1.5px solid var(--rule);
    padding-bottom: 3px; line-height: 28px;
  }
  .appt-field--name { top: 323px; }
  .appt-field--date { top: 382px; }
  .appt-field--time { top: 442px; }

  .appt-note { top: 516px; font-size: 15px; line-height: 22.5px; color: var(--accent); }
</style>
</head>
<body>

<section class="card card--front" aria-label="Business card front">
  <div class="brand-mark"><span class="brand-mark__dot"></span>HPM</div>
  <p class="brand-name">Harbor Pain Management</p>

  <h1 class="doctor-name">DR. MEILIN HART, M.D., PH.D.</h1>
  <p class="doctor-title">Board Certified Anesthiologist</p>

  <div class="icon-row">
    <span class="icon-row__rule"></span>
    <span class="icon-row__icon" aria-label="Phone">
      <svg viewBox="0 0 16 16" fill="#fff"><path d="M2 6c0-2 2-3 6-3s6 1 6 3v1h-3V5.5H5V7H2z"/><rect x="3" y="8" width="10" height="5" rx="1"/></svg>
    </span>
    <span class="icon-row__icon" aria-label="Fax">
      <svg viewBox="0 0 16 16" fill="#fff"><rect x="4" y="1.5" width="8" height="4"/><rect x="1.5" y="6" width="13" height="6" rx="1"/><rect x="4" y="10" width="8" height="4.5" fill="#fff" stroke="#e8590c" stroke-width="1"/></svg>
    </span>
    <span class="icon-row__icon" aria-label="Website">
      <svg viewBox="0 0 16 16" fill="none" stroke="#fff" stroke-width="1.4"><circle cx="8" cy="8" r="6"/><path d="M2 8h12M8 2c-3 3-3 9 0 12M8 2c3 3 3 9 0 12"/></svg>
    </span>
    <span class="icon-row__icon" aria-label="Email">
      <svg viewBox="0 0 16 16" fill="none" stroke="#fff" stroke-width="1.4"><rect x="1.5" y="3.5" width="13" height="9"/><path d="M1.5 3.5 8 9l6.5-5.5"/></svg>
    </span>
    <span class="icon-row__rule"></span>
  </div>

  <ul class="contact-list">
    <li>973.555.0142</li>
    <li>973.555.0187</li>
    <li>www.harborpm.com</li>
    <li>frontdesk.service@harborpm.com</li>
  </ul>

  <div class="divider"></div>

  <address class="address">18 Corvell Road, Suite 304<br>Brisdale, NJ 07391</address>
</section>

<section class="card card--back" aria-label="Business card back">
  <div class="brand-mark"><span class="brand-mark__dot"></span>HPM</div>
  <h2 class="appointment-title">APPOINTMENT</h2>
  <div class="appt-field appt-field--name">NAME:</div>
  <div class="appt-field appt-field--date">DATE :</div>
  <div class="appt-field appt-field--time">TIME :</div>
  <p class="appt-note">If unable to keep your appointment,<br>please contact us as soon as possible</p>
</section>

</body>
</html>
```